Marrowby Water Taxi and Transport Business Card

I need business cards for my new water taxi and freight transport business I have started here in Kodiak Alaska. Kodiak is a remote island in the middle of the gulf of Alaska. There are seven native villages around the island and Kodiak is the #2 fishing port in the United States. We also have the largest Coast Guard Base in the U.S. My company will be providing water taxi and freight transport logistics to the villages and many hunting and fishing lodges as well as remote properties around the island.

I would like a business card that isn't status quo, something that stands out, either in feel or appearance. I do like clean minimal designs but it needs to have the necessary contact info on it.

Target Market(s)

remote lodge / property owners, residents of the many villages around Kodiak and any one wanting to enjoy the great outdoors of Kodiak Alaska

Industry/Entity Type

Business

Contact Information for Business Card

I like clean simple designs that aren't cluttered but still provide the necessary information

Colors
0255a3
3277b5
33a4d5
9bcb3c
add136
fbed22
ffc214
f78f20
f37122

Requirements
Must have
• logo and contact info
• Captain Mason Elwick
• www.marrowbyferryline.com
• mason@marrowbyferryline.com

```html
<!DOCTYPE html>
<html lang="en">
<head>
<meta charset="utf-8">
<title>Marrowby Water Taxi and Transport – Business Card</title>
<link rel="stylesheet" href="https://fonts.googleapis.com/css2?family=Open+Sans:wght@400;600;700&display=swap">
<style>
  :root {
    --navy: #0255a3;
    --blue: #3277b5;
    --sky: #33a4d5;
    --orange: #f78f20;
    --amber: #ffc214;
    --white: #ffffff;
    --stage: #eef1f4;
    --ink-soft: #dbe9f6;
  }
  * { margin: 0; padding: 0; box-sizing: border-box; }
  html, body { width: 1200px; height: 913px; overflow: hidden; }
  body {
    background: var(--stage);
    font-family: "Open Sans", Arial, sans-serif;
    position: relative;
  }
  .card {
    position: absolute;
    top: 308px;
    width: 520px;
    height: 298px;
    border-radius: 16px;
    overflow: hidden;
    box-shadow: 0 6px 18px rgba(0, 40, 80, .18);
  }
  .card-front {
    left: 60px;
    background: linear-gradient(160deg, var(--sky) 0%, var(--blue) 45%, var(--navy) 100%);
    color: var(--white);
  }
  .card-back {
    left: 620px;
    background: var(--white);
  }
  .card-waves { position: absolute; left: 0; bottom: 0; width: 520px; height: 110px; display: block; }
  .divider-line {
    position: absolute; left: 0; right: 0; top: 196px;
    height: 1px; background: var(--orange); opacity: .85;
  }
  .logo-art {
    position: absolute; left: 205px; top: 20px;
    width: 110px; height: 72px; border-radius: 6px;
    background: linear-gradient(180deg, var(--amber) 0%, var(--sky) 45%, #c9ced4 100%);
    opacity: .9;
  }
  .brand {
    position: absolute; left: 0; right: 0; top: 96px;
    text-align: center;
  }
  .brand-name {
    font-weight: 600; font-size: 34px; letter-spacing: 3px; line-height: 1;
  }
  .brand-tagline {
    font-weight: 600; font-size: 14px; letter-spacing: .5px; margin-top: 4px;
  }
  .captain {
    position: absolute; left: 0; right: 0; top: 158px;
    text-align: center; font-weight: 700; font-size: 18px;
  }
  .contact-icons {
    position: absolute; left: 0; right: 0; top: 184px;
    display: flex; justify-content: center; gap: 8px;
  }
  .contact-icons svg { width: 11px; height: 11px; display: block; }
  .contact-line {
    position: absolute; left: 0; right: 0; top: 204px;
    text-align: center; font-size: 12.5px; color: var(--ink-soft);
  }
  .back-art {
    position: absolute; left: 130px; top: 40px;
    width: 260px; height: 170px; border-radius: 8px;
    background: linear-gradient(180deg, #fbc98a 0%, #bfe3f3 40%, #d3d6da 100%);
  }
</style>
</head>
<body>

  <section class="card card-front" aria-label="Business card front">
    <div class="logo-art" role="img" aria-label="Illustration of a water taxi boat before mountains and a rising sun"></div>
    <div class="brand">
      <div class="brand-name">MARROWBY</div>
      <div class="brand-tagline">Water Taxi and Transport</div>
    </div>
    <div class="captain">Captain Mason Elwick</div>
    <div class="contact-icons">
      <svg viewBox="0 0 12 12" aria-hidden="true"><rect x="1" y="2.5" width="10" height="7" fill="none" stroke="#f78f20" stroke-width="1.2"/><path d="M1 3l5 3.5L11 3" fill="none" stroke="#f78f20" stroke-width="1.2"/></svg>
      <svg viewBox="0 0 12 12" aria-hidden="true"><circle cx="6" cy="6" r="4.8" fill="none" stroke="#f78f20" stroke-width="1.2"/><ellipse cx="6" cy="6" rx="2" ry="4.8" fill="none" stroke="#f78f20" stroke-width="1"/><path d="M1.2 6h9.6" stroke="#f78f20" stroke-width="1"/></svg>
    </div>
    <div class="contact-line">mason@marrowbyferryline.com - www.marrowbyferryline.com</div>
    <div class="divider-line"></div>
    <svg class="card-waves" viewBox="0 0 520 110" preserveAspectRatio="none" aria-hidden="true">
      <path d="M0 62 C120 40 220 80 330 52 C410 32 470 20 520 10 L520 110 L0 110Z" fill="var(--orange)"/>
      <path d="M0 82 C130 60 240 96 350 70 C430 52 480 40 520 32 L520 110 L0 110Z" fill="var(--sky)"/>
      <path d="M0 96 C140 80 260 108 380 86 C450 74 490 64 520 58 L520 110 L0 110Z" fill="var(--navy)"/>
    </svg>
  </section>

  <section class="card card-back" aria-label="Business card back">
    <div class="back-art" role="img" aria-label="Illustration of a grey water taxi boat on waves before blue mountains and an orange sun"></div>
    <svg class="card-waves" viewBox="0 0 520 110" preserveAspectRatio="none" aria-hidden="true">
      <path d="M0 70 C140 56 260 86 380 56 C450 40 490 30 520 22 L520 110 L0 110Z" fill="var(--sky)"/>
      <path d="M0 84 C150 70 270 98 390 72 C455 58 495 50 520 44 L520 110 L0 110Z" fill="var(--blue)"/>
      <path d="M0 96 C160 86 280 108 400 90 C460 80 500 72 520 68 L520 110 L0 110Z" fill="var(--navy)"/>
    </svg>
  </section>

</body>
</html>
```